Process Serving Company needs a letterhead design

Looking to have a letterhead designed for letters to attorneys advertising our business. We would like something eye catching but professional. Colors and logos are attached. Please add "Process Service and Attorney Support" near the logo or header

Target Market(s)

Attorneys

Font styles to use
Serif
Sans Serif

Colors
33a6d7
0255a3
85cae6
cee9f5
ecf7fb

```html
<!DOCTYPE html>
<html lang="en">
<head>
<meta charset="utf-8">
<title>Mesa Ridge Process – Letterhead</title>
<link href="https://fonts.googleapis.com/css2?family=Arimo:wght@400;700&family=Open+Sans:wght@400;600&display=swap" rel="stylesheet">
<style>
  :root{
    --brand-blue:#33a6d7;
    --brand-navy:#0255a3;
    --band-blue:#85cae6;
    --ink:#111111;
    --meta:#3a3a3a;
    --paper:#ffffff;
  }
  *{margin:0;padding:0;box-sizing:border-box}
  html,body{width:1059px;height:1200px;overflow:hidden;background:var(--paper)}
  .letterhead{position:relative;width:1059px;height:1200px;background:var(--paper);font-family:"Arimo",Arial,sans-serif;color:var(--ink)}
  .brand{position:absolute;left:118px;top:52px;display:flex;align-items:center;gap:14px}
  .brand-mark{width:30px;height:30px;background:var(--brand-blue)}
  .brand-name{font-family:"Open Sans",sans-serif;font-weight:600;font-size:30px;color:var(--brand-blue);letter-spacing:.5px}
  .header-rule{position:absolute;left:0;top:0}
  .contact{position:absolute;right:77px;top:15px;text-align:right;font-family:"Open Sans",sans-serif;font-size:13px;color:var(--meta);line-height:16px}
  .contact li{list-style:none;display:flex;justify-content:flex-end;align-items:center;gap:6px;height:16.5px}
  .contact svg{width:11px;height:11px;fill:var(--brand-blue)}
  .website{position:absolute;right:72px;top:85px;font-family:"Open Sans",sans-serif;font-size:14.5px;letter-spacing:1px;color:var(--meta)}
  .website b{color:var(--brand-blue);font-weight:600}
  .letter{position:absolute;left:82px;top:262px;width:890px;font-size:17px;line-height:25px}
  .recipient{margin-bottom:10px}
  .letter p.body{margin-bottom:25px}
  .closing{position:absolute;left:82px;top:818px;font-size:17px;line-height:25px}
  .signature{width:150px;height:62px;margin:2px 0 3px;background:linear-gradient(90deg,#e9e9e9,#f6f6f6)}
  .sign-name{font-weight:700}
  .foot-band{position:absolute;left:0;bottom:0;width:100%;height:7px;background:var(--band-blue)}
</style>
</head>
<body>
<div class="letterhead">
  <svg class="header-rule" width="1059" height="140" viewBox="0 0 1059 140" aria-hidden="true">
    <defs>
      <linearGradient id="ruleFade" x1="0" x2="1">
        <stop offset="0" stop-color="#33a6d7" stop-opacity="0"/>
        <stop offset=".15" stop-color="#33a6d7"/>
      </linearGradient>
    </defs>
    <polyline points="66,128 454,128 490,94 796,94" fill="none" stroke="url(#ruleFade)" stroke-width="2.5"/>
  </svg>

  <div class="brand">
    <span class="brand-mark"></span>
    <span class="brand-name">Mesa Ridge Process</span>
  </div>

  <ul class="contact">
    <li>480-555-0192 <svg viewBox="0 0 12 12"><path d="M2 1l2 0 1 3-1.5 1a7 7 0 0 0 3.5 3.5L8 7l3 1v2a1 1 0 0 1-1 1A9 9 0 0 1 1 2a1 1 0 0 1 1-1z"/></svg></li>
    <li>480-555-0192 <svg viewBox="0 0 12 12"><rect x="1" y="5" width="10" height="5" rx="1"/><rect x="3" y="2" width="6" height="3"/></svg></li>
    <li>info@mesaridge.com <svg viewBox="0 0 12 12"><path d="M1 3h10v7H1z M1 3l5 4 5-4" stroke="#fff" stroke-width=".8"/></svg></li>
    <li>2140 E Canyon Ave #204 Tempe AZ 85281 <svg viewBox="0 0 12 12"><path d="M6 1a3.5 3.5 0 0 1 3.5 3.5C9.5 7 6 11 6 11S2.5 7 2.5 4.5A3.5 3.5 0 0 1 6 1zm0 2a1.5 1.5 0 1 0 0 3 1.5 1.5 0 0 0 0-3z"/></svg></li>
  </ul>
  <div class="website">www.<b>mesaridge</b>.com</div>

  <main class="letter">
    <p>Lorem Ipsum</p>
    <p class="recipient">Lorem Ipsum Admin</p>
    <p class="body">Lorem Ipsum is simply dummy text of the printing and typesetting industry. Lorem Ipsum has been the industry's standard dummy text ever since the 1500s, when an unknown printer took a galley of type and scrambled it to make a type specimen book. It has survived not only five centuries, but also the leap into electronic typesetting, remaining essentially unchanged.</p>
    <p class="body">Lorem Ipsum is simply dummy text of the printing and typesetting industry. Lorem Ipsum has been the industry's standard dummy text ever since the 1500s, when an unknown printer took a galley of type and scrambled it to make a type specimen book.</p>
    <p class="body">It has survived not only five centuries, but also the leap into electronic typesetting, remaining essentially unchanged. Lorem Ipsum is simply dummy text of the printing and typesetting industry. Lorem Ipsum has been the industry's standard dummy text ever since the 1500s, when an unknown printer took a galley of type and scrambled</p>
    <p class="body">Lorem Ipsum is simply dummy text of the printing and typesetting industry. Lorem Ipsum has been the industry's standard dummy text ever since the 1500s, when an unknown printer took a galley of type and scrambled it to make a type specimen book. It has survived not only five centuries, but also the leap into electronic typesetting, remaining essentially unchanged.</p>
  </main>

  <footer class="closing">
    <p>Lorem Ipsum</p>
    <div class="signature" role="img" aria-label="Handwritten signature of the sender"></div>
    <p class="sign-name">Lorem Ipsum Admin</p>
  </footer>

  <div class="foot-band"></div>
</div>
</body>
</html>
```